Business card design for sustainable building and development company

Need a business card design for a new sustainable building and real estate development company in the San Francisco Bay area. Name of company is "Tovrin Advisors, LLC" and we provide "Sustainable building, energy and development services" for residential and non residential projects. We'd like the following colors used but not all area required: green, gray, blue. Design should communicate innovation, professionalism and sustainability. Our current website is www.tovrin-advisors.example. Another possible design idea is to have the following listed on the back of the card:
Certified: VERN QS, Eco Marker Rater, DOLM Rater, Terravue Inspector, KSO TQ Building Analyst. Its not a must but could be text that could be used for back of card. Overall, we are open to a simple, clean design and or one with more text than usual for a card.

Industry/Entity Type

Real Estate

Contact Information for Business Card

Name on card: Mark J. Halvik
Title for Name: Principal + Founder
Phone: 555.814.0627
Email: mhalvik@tovrin-advisors.example
Website: www.tovrin-advisors.example

Also, please add the following for address:
Port Elnmere, Westland

Requirements
Nice to have
• If you can integrate the outline of a skyline on the backside of the card and if it looks good, I would like to see the design
Should not have
• a barcode;

```html
<!DOCTYPE html>
<html lang="en">
<head>
<meta charset="utf-8">
<title>Tovrin Advisors – Business Card</title>
<link href="https://fonts.googleapis.com/css2?family=Montserrat:wght@700&family=Open+Sans:wght@400;600&display=swap" rel="stylesheet">
<style>
  :root {
    --green-light: #5db43b;
    --green-dark: #449a3b;
    --brand-green: #58ab2f;
    --paper: #f3f3f1;
    --ink: #1f1f1f;
    --ink-soft: #5a5a5a;
    --backdrop: #d9dbd8;
  }
  * { margin: 0; padding: 0; box-sizing: border-box; }
  html, body { width: 1200px; height: 1029px; overflow: hidden; background: var(--backdrop); }
  .canvas { position: relative; width: 1200px; height: 1029px; }
  .card {
    position: absolute; left: 250px; width: 700px; height: 400px;
    background: var(--paper); overflow: hidden;
    box-shadow: 0 6px 18px rgba(0,0,0,.18);
  }
  .card--back { top: 80px; }
  .card--front { top: 549px; }
  .card__shapes { position: absolute; inset: 0; width: 700px; height: 400px; }
  .brand { position: absolute; display: flex; align-items: center; gap: 12px; }
  .brand__dot { width: 46px; height: 46px; border-radius: 50%; background: var(--brand-green); flex: none; }
  .brand__name {
    font-family: "Montserrat", sans-serif; font-weight: 700; font-size: 30px;
    color: var(--brand-green); line-height: 1; white-space: nowrap;
  }
  .brand__tagline {
    font-family: "Open Sans", sans-serif; font-weight: 600; font-size: 8.5px;
    letter-spacing: .3px; color: var(--ink-soft); text-transform: uppercase; margin-top: 4px;
    white-space: nowrap;
  }
  .card--back .brand { left: 330px; top: 135px; }
  .card--back .website {
    position: absolute; left: 410px; top: 300px;
    font-family: "Open Sans", sans-serif; font-size: 15px; letter-spacing: 1px; color: var(--ink);
    white-space: nowrap;
  }
  .card--front .brand { left: 34px; top: 38px; }
  .person { position: absolute; left: 40px; top: 160px; font-family: "Open Sans", sans-serif; }
  .person__name { font-size: 24px; letter-spacing: 2px; color: var(--ink); text-transform: uppercase; white-space: nowrap; }
  .person__title { font-size: 14px; letter-spacing: 1.5px; color: var(--ink-soft); text-transform: uppercase; margin-left: 140px; }
  .contacts { position: absolute; left: 40px; top: 238px; list-style: none; font-family: "Open Sans", sans-serif; }
  .contacts li { display: flex; align-items: center; gap: 12px; font-size: 12.5px; letter-spacing: .8px; color: var(--ink); height: 22px; text-transform: uppercase; white-space: nowrap; }
  .contacts svg { width: 12px; height: 12px; fill: var(--ink); flex: none; }
</style>
</head>
<body>
<main class="canvas">

  <section class="card card--back" aria-label="Card back">
    <svg class="card__shapes" viewBox="0 0 700 400" aria-hidden="true">
      <rect width="700" height="400" fill="var(--green-light)"/>
      <polygon points="180,0 420,0 225,190" fill="var(--green-dark)"/>
      <polygon points="420,0 700,0 700,400 300,400 225,190" fill="var(--paper)"/>
    </svg>
    <div class="brand">
      <span class="brand__dot"></span>
      <div>
        <div class="brand__name">Tovrin Advisors</div>
        <div class="brand__tagline">Green building, power &amp; growth advisory services</div>
      </div>
    </div>
    <p class="website">WWW.TOVRIN-ADVISORS.EXAMPLE</p>
  </section>

  <section class="card card--front" aria-label="Card front">
    <svg class="card__shapes" viewBox="0 0 700 400" aria-hidden="true">
      <rect width="700" height="400" fill="var(--green-light)"/>
      <polygon points="400,0 700,0 700,60 560,250" fill="var(--green-dark)"/>
      <polygon points="0,0 400,0 560,250 300,400 0,400" fill="var(--paper)"/>
    </svg>
    <div class="brand">
      <span class="brand__dot"></span>
      <div>
        <div class="brand__name">Tovrin Advisors</div>
        <div class="brand__tagline">Green building, power &amp; growth advisory services</div>
      </div>
    </div>
    <div class="person">
      <p class="person__name">Mark J. Halvik</p>
      <p class="person__title">Principal</p>
    </div>
    <ul class="contacts">
      <li><svg viewBox="0 0 24 24"><path d="M6.6 10.8a15 15 0 0 0 6.6 6.6l2.2-2.2a1 1 0 0 1 1-.25 11.4 11.4 0 0 0 3.6.57 1 1 0 0 1 1 1V20a1 1 0 0 1-1 1A17 17 0 0 1 3 4a1 1 0 0 1 1-1h3.5a1 1 0 0 1 1 1c0 1.25.2 2.45.57 3.57a1 1 0 0 1-.25 1z"/></svg>555.814.0627</li>
      <li><svg viewBox="0 0 24 24"><path d="M2 5h20v14H2z"/><path d="M3 6l9 7 9-7" fill="none" stroke="var(--paper)" stroke-width="1.6"/></svg>mhalvik@tovrin-advisors.example</li>
      <li><svg viewBox="0 0 24 24"><circle cx="12" cy="12" r="10"/></svg>www.tovrin-advisors.example</li>
      <li><svg viewBox="0 0 24 24"><path d="M12 2a7 7 0 0 0-7 7c0 5 7 13 7 13s7-8 7-13a7 7 0 0 0-7-7zm0 9.5A2.5 2.5 0 1 1 12 6.5a2.5 2.5 0 0 1 0 5z"/></svg>Port Elnmere, Westland</li>
    </ul>
  </section>

</main>
</body>
</html>
```